Indy Film Production Company/Studio

We need a business card designed from an existing logo. We are a digital studio/production company that caters to creating genre entertainment, like Action, Horror, and martial arts. The card along with the logo will be used to Brand the company from letter heads to banners. The design will also be used for postcards and Brochures. It should be professional and masculine.
Updates

Thank you to all the designers who have participated. I'm narrowing down who it will be. Thank you again.

Target Market(s)

Investors, Networks, Producers, and actors

Industry/Entity Type

Film Production

Contact Information for Business Card

Teodoro Valbuena
Producer/Writer/Director
www.kestrelpicturehouse.example

Requirements
Must have
• Website address, Facebook icon and Twitter icon possibly in the back of the card.
Nice to have
• Logline of Company: Follow The Action.

```html
<!DOCTYPE html>
<html lang="en">
<head>
<meta charset="utf-8">
<title>Kestrel Picture House – Business Card</title>
<link rel="stylesheet" href="https://fonts.googleapis.com/css2?family=Montserrat:ital,wght@1,800&family=Roboto:wght@400;900&display=swap">
<style>
  :root {
    --backdrop: #a9a7a7;
    --card: #2e2b2a;
    --brand-red: #d3302a;
    --text-light: #e6e4e2;
    --divider: #6b6866;
  }
  * { margin: 0; padding: 0; box-sizing: border-box; }
  html, body {
    width: 1200px; height: 1200px; overflow: hidden;
    background: var(--backdrop);
    font-family: "Roboto", Arial, sans-serif;
  }
  .canvas { position: relative; width: 1200px; height: 1200px; }
  .card {
    position: absolute;
    width: 713px; height: 418px;
    background: var(--card);
  }
  .card--front { left: 238px; top: 118px; }
  .card--back { left: 231px; top: 643px; }

  .wordmark {
    position: absolute;
    color: var(--brand-red);
    font-family: "Roboto", Arial, sans-serif;
    font-weight: 900;
    text-transform: uppercase;
    text-align: center;
    line-height: 1;
  }
  .wordmark__main { display: block; }
  .wordmark__sub { display: block; letter-spacing: 0.02em; }

  .card--front .wordmark { left: 0; right: 0; top: 140px; }
  .card--front .wordmark__main { font-size: 82px; letter-spacing: 0.01em; }
  .card--front .wordmark__sub { font-size: 27px; margin-top: 12px; }

  .card--back .wordmark { left: 44px; width: 260px; top: 158px; }
  .card--back .wordmark__main { font-size: 60px; }
  .card--back .wordmark__sub { font-size: 20px; margin-top: 10px; }

  .divider {
    position: absolute; left: 337px; top: 72px;
    width: 1px; height: 275px; background: var(--divider);
  }
  .contact { position: absolute; left: 374px; top: 112px; color: var(--text-light); }
  .contact__name {
    font-family: "Montserrat", Arial, sans-serif;
    font-style: italic; font-weight: 800;
    font-size: 25px; color: var(--brand-red); line-height: 1;
  }
  .contact__title { font-size: 16.5px; margin-top: 10px; }
  .contact__list { list-style: none; margin-top: 27px; font-size: 18px; }
  .contact__item { display: flex; align-items: center; height: 28px; }
  .contact__icon { width: 17px; height: 14px; margin-right: 18px; flex: none; }
  .contact__address { font-size: 18px; line-height: 28px; margin-top: 2px; }
</style>
</head>
<body>
<main class="canvas">
  <section class="card card--front" aria-label="Card front">
    <div class="wordmark">
      <span class="wordmark__main">Kestrel</span>
      <span class="wordmark__sub">Picture House</span>
    </div>
  </section>

  <section class="card card--back" aria-label="Card back">
    <div class="wordmark">
      <span class="wordmark__main">Kestrel</span>
      <span class="wordmark__sub">Picture House</span>
    </div>
    <div class="divider"></div>
    <div class="contact">
      <p class="contact__name">Teodoro Valbuena</p>
      <p class="contact__title">Managing Director</p>
      <ul class="contact__list">
        <li class="contact__item">
          <svg class="contact__icon" viewBox="0 0 17 14" aria-hidden="true">
            <path d="M1 5 Q8.5 0 16 5 L14 7 L12 5.5 L5 5.5 L3 7 Z" fill="#d3302a"/>
            <rect x="3" y="7" width="11" height="6" rx="1" fill="#d3302a"/>
          </svg>
          <span>+00 111 222 3333</span>
        </li>
        <li class="contact__item">
          <svg class="contact__icon" viewBox="0 0 17 14" aria-hidden="true">
            <rect x="1" y="2" width="15" height="10" fill="#d3302a"/>
            <path d="M1 2 L8.5 8 L16 2" fill="none" stroke="#2e2b2a" stroke-width="1.4"/>
          </svg>
          <span>yourname@yourwebsite.com</span>
        </li>
      </ul>
      <p class="contact__address">Your Long Commercial or<br>business address in 2 line</p>
    </div>
  </section>
</main>
</body>
</html>
```